Business Card for a mobile physiotherapy company

I need a layout for a business card for a mobile physiotherapy company.
Slogan is "Mobile Physiotherapy - Your Road To Recovery"
Phone number is 867-555-0142
Email VardenTherapy@postnest.ca (subject to change with website)
Website www.VardenTherapy.ca
My name and credentials: Luke Varden Luke Varden, BSc(kin), MPT, CAFCI, IMS
Information maybe included: Direct Billing, Services including Physiotherapy, IMS, acupuncture
Maybe include facebook and instagram logos
One side with the logo clean and sharp
Other side with details, try not to look too busy, keep everything concise

```html
<!DOCTYPE html>
<html lang="en">
<head>
<meta charset="utf-8">
<title>Varden Therapy – Business Card</title>
<link href="https://fonts.googleapis.com/css2?family=Alegreya:wght@400;700&display=swap" rel="stylesheet">
<style>
  :root {
    --backdrop: #cfcfcf;
    --teal: #1b5a55;
    --navy: #27446d;
    --navy-dark: #253f68;
    --green: #1b5646;
    --paper: #f4f4f4;
    --paper-shade: #e1e1e1;
    --ink-soft: #4a4f59;
    --white: #f4f5f6;
  }
  * { margin: 0; padding: 0; box-sizing: border-box; }
  html, body {
    width: 1200px; height: 576px; overflow: hidden;
    background: var(--backdrop);
    font-family: "Alegreya", Georgia, serif;
  }
  .card {
    position: absolute; top: 138px;
    width: 484px; height: 294px;
    border-radius: 14px; overflow: hidden;
    box-shadow: 0 3px 6px rgba(0,0,0,0.25);
  }
  /* Front */
  .card-front {
    left: 82px;
    background: linear-gradient(120deg, var(--teal) 0%, var(--navy) 70%);
    color: var(--white); text-align: center;
  }
  .front-name {
    position: absolute; top: 112px; left: 0; right: 0;
    font-size: 44px; font-weight: 700; line-height: 1;
    color: var(--white);
  }
  .brand-rule {
    position: absolute; top: 180px; left: 111px; width: 262px; height: 2px;
    background: var(--white);
  }
  .front-tagline {
    position: absolute; top: 185px; left: 0; right: 0;
    font-size: 11.5px;
  }
  .front-services {
    position: absolute; top: 261px; left: 0; right: 0;
    font-size: 12.5px; letter-spacing: 0.2px;
  }
  /* Back */
  .card-back {
    left: 602px;
    background: linear-gradient(160deg, var(--paper) 0%, var(--paper-shade) 100%);
  }
  .person-name {
    position: absolute; left: 24px; top: 55px;
    font-size: 22px; font-weight: 700; color: var(--navy-dark); letter-spacing: 0.5px;
  }
  .credentials {
    position: absolute; left: 24px; top: 84px;
    font-size: 11px; color: var(--ink-soft);
  }
  .contact-list {
    position: absolute; left: 24px; top: 180px; list-style: none;
    font-size: 13px; color: var(--ink-soft);
  }
  .contact-list li { display: flex; align-items: center; height: 17.5px; }
  .contact-list svg { width: 10px; height: 10px; margin-right: 14px; fill: var(--green); }
  .follow {
    position: absolute; left: 24px; top: 243px;
    font-size: 13px; color: var(--ink-soft);
    display: flex; align-items: center;
  }
  .social-dot {
    width: 20px; height: 20px; border-radius: 50%; margin-left: 5px;
    background: var(--navy);
  }
  .social-dot:first-of-type { margin-left: 8px; }
  .back-name {
    position: absolute; right: 24px; top: 118px; width: 200px;
    text-align: center; font-size: 26px; font-weight: 700; line-height: 1;
    color: var(--navy-dark);
  }
  .green-strip {
    position: absolute; left: 0; bottom: 0; width: 200px; height: 12px;
    background: var(--green);
  }
  .tagline-tab {
    position: absolute; right: 0; bottom: 0; width: 300px; height: 36px;
    background: var(--navy-dark);
    clip-path: polygon(14px 0, 100% 0, 100% 100%, 0 100%);
    color: var(--white); font-size: 11.5px;
    display: flex; align-items: center; justify-content: center; padding-left: 12px;
  }
</style>
</head>
<body>
  <section class="card card-front">
    <p class="front-name">Varden Therapy</p>
    <div class="brand-rule"></div>
    <p class="front-tagline">Mobile Physiotherapy - Your Road To Recovery</p>
    <p class="front-services">Direct Billing &nbsp;|&nbsp; Services Including Physiotherapy &nbsp;|&nbsp; IMS &nbsp;|&nbsp; Acupuncture</p>
  </section>

  <section class="card card-back">
    <h1 class="person-name">LUKE VARDEN</h1>
    <p class="credentials">BSc(kin), MPT, CAFCI, IMS</p>
    <ul class="contact-list">
      <li><svg viewBox="0 0 10 10"><path d="M1 3 Q5 0 9 3 L8 5 L6.5 4 L6.5 3.2 Q5 2.8 3.5 3.2 L3.5 4 L2 5 Z M2.5 5.5 H7.5 L8.5 9 H1.5 Z"/></svg>867-555-0142</li>
      <li><svg viewBox="0 0 10 10"><path d="M0.5 2 H9.5 V8 H0.5 Z M1.2 2.6 L5 5.6 L8.8 2.6" stroke="#f4f4f4" stroke-width="0.8"/></svg>VardenTherapy@postnest.ca</li>
      <li><svg viewBox="0 0 10 10"><circle cx="5" cy="5" r="4.5"/><path d="M0.5 5 H9.5 M5 0.5 V9.5" stroke="#f4f4f4" stroke-width="0.7"/></svg>www.VardenTherapy.ca</li>
    </ul>
    <div class="follow">Follow us on:<span class="social-dot"></span><span class="social-dot"></span></div>
    <p class="back-name">Varden Therapy</p>
    <div class="green-strip"></div>
    <div class="tagline-tab">Mobile Physiotherapy - Your Road To Recovery</div>
  </section>
</body>
</html>
```